TA BRAMLEY BUSINESS CARD DESIGN PROJECT

We need to utilize our logo that was expertly created on PixelHarbor and now need to match this with a business card design.

```html
<!DOCTYPE html>
<html lang="en">
<head>
<meta charset="utf-8">
<title>TA Bramley — Business Card</title>
<link rel="stylesheet" href="https://fonts.googleapis.com/css2?family=Open+Sans:wght@400;600;700&display=swap">
<style>
  :root {
    --stage: #222222;
    --card-white: #ffffff;
    --card-black: #1c1c22;
    --brand-blue: #1556a8;
    --ink: #111111;
    --emboss: #2c2c34;
  }
  * { box-sizing: border-box; margin: 0; padding: 0; }
  html, body { width: 1200px; height: 780px; overflow: hidden; }
  body {
    background: var(--stage);
    font-family: "Open Sans", Arial, sans-serif;
    position: relative;
  }
  .card {
    position: absolute;
    top: 242px;
    width: 520px;
    height: 297px;
    border-radius: 2px;
    overflow: hidden;
  }
  .card--front { left: 50px; background: var(--card-white); }
  .card--back { left: 630px; background: var(--card-black); }

  .front__brand {
    position: absolute;
    left: 20px;
    top: 92px;
    width: 222px;
    text-align: center;
    color: var(--brand-blue);
    font-weight: 700;
    font-size: 26px;
    letter-spacing: 2px;
    line-height: 1;
    white-space: nowrap;
  }
  .front__divider {
    position: absolute;
    left: 262px;
    top: 40px;
    width: 1px;
    height: 170px;
    background: var(--ink);
    opacity: 0.8;
  }
  .contact {
    position: absolute;
    left: 292px;
    top: 56px;
    color: var(--ink);
  }
  .contact__name {
    color: var(--brand-blue);
    font-weight: 700;
    font-size: 26px;
    line-height: 1.1;
    white-space: nowrap;
  }
  .contact__role {
    font-size: 13px;
    margin: 4px 0 14px;
  }
  .contact__list { list-style: none; font-size: 13.5px; line-height: 1.55; }
  .contact__list li { display: flex; align-items: center; gap: 7px; white-space: nowrap; }
  .contact__icon { width: 12px; height: 12px; fill: var(--brand-blue); flex: none; }

  .address-band {
    position: absolute;
    left: 0; right: 0; bottom: 22px;
    height: 26px;
    background: var(--brand-blue);
    display: flex;
    align-items: center;
    padding-left: 30px;
  }
  .address-band__text {
    color: var(--card-white);
    font-size: 13px;
    letter-spacing: 0.2px;
    white-space: nowrap;
  }

  .back__brand {
    position: absolute;
    inset: 0;
    display: flex;
    align-items: center;
    justify-content: center;
    color: var(--emboss);
    font-weight: 700;
    font-size: 44px;
    letter-spacing: 6px;
    white-space: nowrap;
  }
</style>
</head>
<body>
  <section class="card card--front" aria-label="Business card front">
    <div class="front__brand">TA BRAMLEY</div>
    <div class="front__divider" aria-hidden="true"></div>
    <div class="contact">
      <div class="contact__name">Lena Marsh</div>
      <div class="contact__role">Managing Director</div>
      <ul class="contact__list">
        <li>
          <svg class="contact__icon" viewBox="0 0 24 24" aria-hidden="true"><path d="M6.6 10.8a15.1 15.1 0 0 0 6.6 6.6l2.2-2.2a1 1 0 0 1 1-.25 11.4 11.4 0 0 0 3.6.57 1 1 0 0 1 1 1V20a1 1 0 0 1-1 1A17 17 0 0 1 3 4a1 1 0 0 1 1-1h3.5a1 1 0 0 1 1 1c0 1.25.2 2.45.57 3.57a1 1 0 0 1-.25 1z"/></svg>
          (555) 214-0386
        </li>
        <li>
          <svg class="contact__icon" viewBox="0 0 24 24" aria-hidden="true"><path d="M2 5h20v14H2zm2 2v.5l8 5 8-5V7zm0 2.8V17h16V9.8l-8 5z"/></svg>
          info@tabramley.com
        </li>
        <li>
          <svg class="contact__icon" viewBox="0 0 24 24" aria-hidden="true"><path d="M12 2a10 10 0 1 0 0 20 10 10 0 0 0 0-20zm6.9 6h-3a15.7 15.7 0 0 0-1.4-3.6A8 8 0 0 1 18.9 8zM12 4a14 14 0 0 1 1.9 4h-3.8A14 14 0 0 1 12 4zM4.3 14a8 8 0 0 1 0-4h3.4a16 16 0 0 0 0 4zm.8 2h3a15.7 15.7 0 0 0 1.4 3.6A8 8 0 0 1 5.1 16zm3-8h-3a8 8 0 0 1 4.4-3.6A15.7 15.7 0 0 0 8.1 8zM12 20a14 14 0 0 1-1.9-4h3.8A14 14 0 0 1 12 20zm2.3-6H9.7a14.7 14.7 0 0 1 0-4h4.6a14.7 14.7 0 0 1 0 4zm.2 5.6a15.7 15.7 0 0 0 1.4-3.6h3a8 8 0 0 1-4.4 3.6zM16.3 14a16 16 0 0 0 0-4h3.4a8 8 0 0 1 0 4z"/></svg>
          www.tabramley.com
        </li>
      </ul>
    </div>
    <div class="address-band">
      <span class="address-band__text">418 Willow Crest Ave. Suite 120 Brookfield, TX 75001</span>
    </div>
  </section>

  <section class="card card--back" aria-label="Business card back">
    <div class="back__brand">TA BRAMLEY</div>
  </section>
</body>
</html>
```